A Health & Fitness Website selling saunas and Cold tubs

www.dockvaultguys.com, www.frostlanterguys, www.chillharborguys
Design a website
We are selling saunas, infrared saunas, cold plunge tubs, and massage chairs to financially successful MEN.
We want professional, simple, masculine with a touch of sexy.
One section for each… saunas, cold plunge tubs, massage chairs.
Each will have at least two buy links to their affiliate/supplier/store.
The landing page / opening page / needs big & bold; a full screen image? a great picture showing the warmth of a sauna? Need your ideas
The pictures are everything.

The Website for our book
https://maebelsvigorguys.com/

Coding

Coded - Design and coding required

Number of Pages Required

1 page

Requirements
Must have
• Great pictures

```html
<!DOCTYPE html>
<html lang="en">
<head>
<meta charset="utf-8">
<title>Maebel's Vigor Guys — Saunas, Cold Plunge Tubs &amp; Massage Chairs</title>
<link href="https://fonts.googleapis.com/css2?family=Poppins:wght@600;700;800&family=Roboto:wght@400;500;700&display=swap" rel="stylesheet">
<style>
:root{
  --orange:#ea4a1c;
  --orange-light:#f47a2c;
  --ink:#111111;
  --dark:#151515;
  --text:#3d3d3d;
  --muted:#6a6a6a;
  --white:#ffffff;
  --card-shadow:0 6px 28px rgba(0,0,0,.08);
}
*{margin:0;padding:0;box-sizing:border-box}
html,body{width:1200px;height:4511px;overflow:hidden;background:var(--white)}
body{position:relative;font-family:"Roboto",Arial,sans-serif;color:var(--text)}
.abs{position:absolute}

/* Hero */
.hero{left:0;top:0;width:1200px;height:720px;background:var(--dark);overflow:hidden}
.hero-topline{left:0;top:0;width:1200px;height:5px;background:var(--orange)}
.hero-photo{left:560px;top:5px;width:640px;height:700px;background:linear-gradient(160deg,#3a3c42 0%,#2a2b2f 45%,#4a4840 75%,#1d1d1d 100%)}
.hero-wave{left:0;top:560px;width:1200px;height:170px}
.brand{left:108px;top:60px;display:flex;align-items:center;gap:12px}
.brand-dot{width:42px;height:42px;border-radius:50%;border:3px solid var(--white)}
.brand-name{font-family:"Poppins",sans-serif;font-weight:700;font-size:20px;color:var(--white);line-height:1.1;width:150px}
.hero-title{left:108px;top:232px;font-family:"Poppins",sans-serif;font-weight:800;font-size:38px;line-height:57px;color:var(--white);text-transform:uppercase}
.hero-sub{left:108px;top:412px;font-size:15px;line-height:33px;color:#e8e8e8;width:410px}
.btn{display:inline-flex;align-items:center;justify-content:center;background:var(--orange);color:var(--white);font-family:"Roboto",sans-serif;font-weight:500;font-size:15px;border-radius:24px;height:42px;text-decoration:none}
.hero-btn{left:108px;top:494px;width:125px}

/* Circulation section */
.section-title{left:0;width:1200px;text-align:center;font-family:"Poppins",sans-serif;font-weight:800;font-size:37px;line-height:64px;color:var(--ink);text-transform:uppercase}
.circ-title{top:792px}
.round-photo-ring{left:103px;top:990px;width:380px;height:385px}
.round-photo{left:128px;top:966px;width:395px;height:395px;border-radius:50%;background:radial-gradient(circle at 45% 40%,#e9e1da 0%,#cfc2b8 55%,#a89586 100%)}
.benefit-lead{left:583px;top:954px;width:440px;font-weight:500;font-size:17px;line-height:36px;color:var(--orange)}
.benefits{top:1046px;list-style:none;font-size:13.5px;color:var(--muted)}
.benefits li{position:relative;height:35px;line-height:35px;padding-left:34px;white-space:nowrap}
.benefits li::before{content:"»";position:absolute;left:0;top:0;color:var(--orange);font-weight:700;font-size:15px}
.benefits li.cont::before{content:""}
.benefits-a{left:583px;width:275px}
.benefits-b{left:858px;width:260px}
.benefit-note{left:583px;top:1344px;font-weight:500;font-size:15.5px;color:var(--ink)}

/* Product cards */
.product{left:42px;width:1114px;height:511px;border-radius:8px;overflow:hidden}
.product-sauna{top:1486px;background:linear-gradient(100deg,#8a5a2a 0%,#c7893f 35%,#e8b766 60%,#d49a52 100%)}
.product-cold{top:2060px;background:linear-gradient(100deg,#e9e9ea 0%,#b9a7a2 40%,#6b5550 70%,#d8d8da 100%)}
.product-chair{top:2632px;background:linear-gradient(100deg,#f1efec 0%,#c9c4bd 35%,#3b3a3a 55%,#e2ddd7 100%)}
.badge-ring{width:380px;height:380px;border-radius:50%;background:rgba(255,255,255,.82)}
.badge{width:326px;height:326px;border-radius:50%;background:linear-gradient(160deg,var(--orange-light) 0%,var(--orange) 60%,#d8361a 100%);display:flex;flex-direction:column;align-items:center;justify-content:center;text-align:center;color:var(--white);padding:0 28px}
.badge h2{font-family:"Poppins",sans-serif;font-weight:800;font-size:38px;line-height:48px;text-transform:uppercase}
.badge p{font-size:13.5px;line-height:27px;margin-top:10px}
.badge .btn-light{margin-top:20px;background:var(--white);color:var(--orange);width:124px;height:42px;border-radius:24px;display:inline-flex;align-items:center;justify-content:center;font-weight:500;font-size:15px;text-decoration:none}

/* Testimonials */
.blood-title{top:3237px}
.quote{width:314px;height:394px;background:var(--white);box-shadow:var(--card-shadow);border-radius:4px;padding:36px 26px 0}
.quote svg{display:block;margin-bottom:18px}
.quote p{font-size:12.5px;line-height:25.5px;color:var(--muted)}
.row1{top:3411px}
.row2{top:3840px}
.col1{left:89px}.col2{left:443px}.col3{left:797px}
.cta-book{left:464px;top:4276px;width:125px;height:44px}
.cta-start{left:610px;top:4276px;width:126px;height:44px}

/* Footer */
.footer{left:0;top:4397px;width:1200px;height:114px;background:var(--dark)}
.copyright{left:80px;top:4446px;font-size:13.5px;color:var(--white)}
.subscribe{left:583px;top:4428px;width:568px;height:56px;border-radius:30px;background:var(--white);display:flex;align-items:center;justify-content:space-between;padding:0 6px 0 40px}
.subscribe span{font-size:14px;color:var(--muted)}
.subscribe .btn{width:178px;height:44px;font-weight:700;font-size:15px}
</style>
</head>
<body>

<section class="hero abs">
  <div class="hero-topline abs"></div>
  <div class="hero-photo abs" role="img" aria-label="Personal trainer coaching a woman lifting a kettlebell in a gym"></div>
  <div class="brand abs"><span class="brand-dot"></span><span class="brand-name">Maebel's Vigor Guys</span></div>
  <h1 class="hero-title abs">Dramatically<br>Improve Your Health<br>Without Exercise</h1>
  <p class="hero-sub abs">Successful Men Recognize the Importance of Their Health and Make it a Priority.&nbsp; It's Your Time.&nbsp; You've Earned it.</p>
  <a class="btn hero-btn abs" href="#">Book Now</a>
</section>
<svg class="hero-wave abs" viewBox="0 0 1200 170" preserveAspectRatio="none" aria-hidden="true">
  <path d="M0 115 C260 20 520 20 780 70 C960 105 1100 100 1200 80 L1200 170 L0 170 Z" fill="#ffffff"/>
  <path d="M110 158 C240 70 460 45 700 85 C900 118 1080 115 1200 95 L1200 112 C1080 140 900 148 700 118 C470 82 260 100 110 175 Z" fill="var(--orange)"/>
</svg>

<h2 class="section-title circ-title abs">A Mans Body Thrives on Circulation &nbsp;&amp; it<br>doesn't care how you get it.</h2>

<svg class="round-photo-ring abs" viewBox="0 0 380 385" aria-hidden="true">
  <path d="M40 10 C-20 110 -5 300 170 370 C260 400 340 370 375 330 C300 370 170 360 95 280 C30 210 20 100 40 10 Z" fill="var(--orange)"/>
</svg>
<div class="round-photo abs" role="img" aria-label="Smiling woman sitting on a studio floor in workout clothes"></div>

<p class="benefit-lead abs">When there's no time for exercise. use Hot, Cold, or Massage. The Benefits are Numerous</p>
<ul class="benefits benefits-a abs">
  <li>Relieve Stress</li>
  <li>Detox Your Pores</li>
  <li>Sleep Better</li>
  <li>Relieve Muscle Tension</li>
  <li>Boost Energy Levels</li>
  <li>Increase Testosterone</li>
  <li>Reduce Inflammation</li>
  <li>Increase Immunity &nbsp;Reduce Depression</li>
</ul>
<ul class="benefits benefits-b abs">
  <li>Alleviate Joint Pain</li>
  <li>Healthier Skin</li>
  <li>Lower the Risk of</li>
  <li class="cont">Cardiovascular Disease</li>
  <li>Increase Metabolism</li>
  <li>Promote Weight Loss</li>
  <li>A Longer &amp; Healthier Life</li>
</ul>
<p class="benefit-note abs">Specific Improvements will be Individual to You.</p>

<section class="product product-sauna abs" role="img" aria-label="Couple relaxing together on the wooden benches of a warm sauna"></section>
<div class="badge-ring abs" style="left:710px;top:1553px"></div>
<div class="badge abs" style="left:737px;top:1580px">
  <h2>Saunas</h2>
  <p>Lorem ipsum dolor sit amet, conse ctetur adipiscing elit, sed do eiusmod tem por incididunt ut labore et dolore</p>
  <a class="btn-light" href="#">Book Now</a>
</div>

<section class="product product-cold abs" role="img" aria-label="Couple embracing in a bubbling tub surrounded by rose petals"></section>
<div class="badge-ring abs" style="left:127px;top:2128px"></div>
<div class="badge abs" style="left:154px;top:2155px">
  <h2>Cold<br>Plunge Tubs</h2>
  <p>Lorem ipsum dolor sit amet, conse ctetur adipiscing elit, sed do eiusmod tem</p>
  <a class="btn-light" href="#">Book Now</a>
</div>

<section class="product product-chair abs" role="img" aria-label="Smiling woman reclining in a white and black massage chair"></section>
<div class="badge-ring abs" style="left:710px;top:2692px"></div>
<div class="badge abs" style="left:737px;top:2719px">
  <h2>Massage<br>Chair</h2>
  <p>Lorem ipsum dolor sit amet, conse ctetur adipiscing elit, sed do eiusmod tem</p>
  <a class="btn-light" href="#">Book Now</a>
</div>

<h2 class="section-title blood-title abs">Everything works better with<br>increased blood flow</h2>

<article class="quote row1 col1 abs">
  <svg width="30" height="24" viewBox="0 0 30 24" aria-hidden="true"><path d="M0 24V13C0 5 4 1 12 0l1 4C8 5 6 8 6 11h6v13zm17 0V13c0-8 4-12 12-13l1 4c-5 1-7 4-7 7h6v13z" fill="var(--orange)"/></svg>
  <p>We're your typical old married couple.&nbsp; After 24 years we don't have sex very often. I had been using my cold plunge for about two months pretty religiously every weekend and I knew the changes it made in me mahood. I had not been that consistently hard in years. One frisky night under the covers with my wife grabbed me and said. Who's dick is that!" Of course it hasn't increased our sex life but dam when we do it feels good to be hard again."</p>
</article>
<article class="quote row1 col2 abs">
  <svg width="30" height="24" viewBox="0 0 30 24" aria-hidden="true"><path d="M0 24V13C0 5 4 1 12 0l1 4C8 5 6 8 6 11h6v13zm17 0V13c0-8 4-12 12-13l1 4c-5 1-7 4-7 7h6v13z" fill="var(--orange)"/></svg>
  <p>"When you do a little homework and learn that deep breathing is a big key too climbing in a cold plunge, you also learn that you can take that breathing exercise with you anywhere. I do deep breathing exercises at my desk every day. I do it before I fall asleep and any time I just want to relax. No water needed."</p>
</article>
<article class="quote row1 col3 abs">
  <svg width="30" height="24" viewBox="0 0 30 24" aria-hidden="true"><path d="M0 24V13C0 5 4 1 12 0l1 4C8 5 6 8 6 11h6v13zm17 0V13c0-8 4-12 12-13l1 4c-5 1-7 4-7 7h6v13z" fill="var(--orange)"/></svg>
  <p>"I hate exercise.&nbsp; I love my work.&nbsp; If I'm not working I'm relaxing and thinking about work. 24/7 I'm on.&nbsp; I have the dual plunge, hot and cold.&nbsp; I use the cold more in the summer, it's incredibly refreshing. I use the hot more in the winter.&nbsp; I occasionally do both but usually I only have time for one.&nbsp; When I'm refreshed, I'm more productive.&nbsp; When I'm productive I make more money.&nbsp; That's what I'm all about."</p>
</article>

<article class="quote row2 col1 abs">
  <svg width="30" height="24" viewBox="0 0 30 24" aria-hidden="true"><path d="M0 24V13C0 5 4 1 12 0l1 4C8 5 6 8 6 11h6v13zm17 0V13c0-8 4-12 12-13l1 4c-5 1-7 4-7 7h6v13z" fill="var(--orange)"/></svg>
  <p>"Owning a sauna has completely revolutionized my wellness routine. I used to struggle to find time for self-care with my busy schedule. Now my sauna is just a few steps away. I can easily prioritize my well-being. The detoxifying sweat, followed by a refreshing shower, leaves me feeling great and ready for the world. It's a well-deserved investment in my health. "</p>
</article>
<article class="quote row2 col2 abs">
  <svg width="30" height="24" viewBox="0 0 30 24" aria-hidden="true"><path d="M0 24V13C0 5 4 1 12 0l1 4C8 5 6 8 6 11h6v13zm17 0V13c0-8 4-12 12-13l1 4c-5 1-7 4-7 7h6v13z" fill="var(--orange)"/></svg>
  <p>"I never thought climbing into a cold tub of ice would be something I could do. At first it was a mental hurdle but when you learn how to breathe before you get in it's so easy it's ridiculous and the after effects are fantastic. The next day I feel like I have a whole new body. I'm a building contractor so I stay pretty physical.&nbsp; Nothing heavy duty but still I'm on my feet all day.&nbsp; My arms are moving.&nbsp; My legs are moving. I'm get pretty sore at the end of the week.</p>
</article>
<article class="quote row2 col3 abs">
  <svg width="30" height="24" viewBox="0 0 30 24" aria-hidden="true"><path d="M0 24V13C0 5 4 1 12 0l1 4C8 5 6 8 6 11h6v13zm17 0V13c0-8 4-12 12-13l1 4c-5 1-7 4-7 7h6v13z" fill="var(--orange)"/></svg>
  <p>"Back in the day you remember Dale Brennan and his fire walks. Well that was freaking crazy.&nbsp; When I first heard about these cold plunges I kind of put it in that category. Crazy, but not as crazy as stepping on hot coals. So I tried it in my bathtub with a couple of bags of ice. I'll be damned how refreshing it was. A little deep breathing to get you started and the rest was pure relaxation. Nobody got that from stepping on hot coals. With my own cold tub it's part of my weekly routine.</p>
</article>

<a class="btn cta-book abs" href="#">Book Now</a>
<a class="btn cta-start abs" href="#">Get Started</a>

<footer class="footer abs"></footer>
<p class="copyright abs">(C) Copyright 2024 | All Rights Reserved.</p>
<div class="subscribe abs"><span>Email Address</span><a class="btn" href="#">Subscribe Now</a></div>

</body>
</html>
```